BRIGHT RIVER POWER.

I'd like my business logo.
contact name: Dennis Halvorsen
phone:0438759164
email: info@brightriverpower.net.au
website: www.brightriverpower.net.au

services:
solar
battery storage
LED lighting
energy saving solutions
general electrical
I'd like the design to look professional

Target Market(s)

Everyone

Industry/Entity Type

Business

Contact Information for Business Card

as described above

Requirements
Must have
• Id like the colours and the design to work well with my logo.

```html
<!DOCTYPE html>
<html lang="en">
<head>
<meta charset="utf-8">
<title>Bright River Power – Business Card</title>
<link href="https://fonts.googleapis.com/css2?family=Open+Sans:wght@400;600;700&display=swap" rel="stylesheet">
<style>
  :root {
    --page-bg: #3f3f3f;
    --card-white: #ffffff;
    --brand-green: #4da33a;
    --brand-green-dark: #3c9a32;
    --brand-green-light: #93c83e;
    --text-grey: #4a4a4a;
    --text-white: #ffffff;
  }
  * { margin: 0; padding: 0; box-sizing: border-box; }
  html, body {
    width: 1105px; height: 1200px; overflow: hidden;
    background: var(--page-bg);
    font-family: "Open Sans", Arial, sans-serif;
  }
  .card {
    position: absolute;
    left: 193px;
    width: 720px;
    height: 410px;
  }
  .card--front { top: 167px; background: var(--card-white); }
  .card--back {
    top: 623px;
    background: radial-gradient(ellipse 70% 75% at 52% 30%, var(--brand-green-light) 0%, #6fb83a 45%, var(--brand-green-dark) 100%);
  }

  .brand-name {
    position: absolute;
    display: flex;
    align-items: center;
    gap: 14px;
    font-weight: 700;
    letter-spacing: 0.5px;
    white-space: nowrap;
  }
  .card--front .brand-name {
    left: 36px; top: 66px;
    font-size: 36px;
    color: var(--brand-green);
  }
  .brand-dot {
    width: 40px; height: 40px;
    border-radius: 50%;
    background: var(--brand-green);
    flex: none;
  }

  .contact-list {
    position: absolute;
    left: 50px; top: 284px;
    list-style: none;
  }
  .contact-item {
    display: flex;
    align-items: center;
    gap: 9px;
    height: 27.5px;
    font-size: 19px;
    color: var(--text-grey);
  }
  .contact-icon { width: 17px; height: 17px; flex: none; fill: var(--brand-green); }

  .contact-name {
    position: absolute;
    right: 46px; top: 312px;
    font-size: 26px;
    font-weight: 700;
    color: var(--brand-green);
  }
  .name-tab {
    position: absolute;
    right: 0; top: 308px;
    width: 18px; height: 39px;
    background: linear-gradient(90deg, var(--brand-green-light), var(--brand-green));
  }

  .service-list {
    position: absolute;
    left: 48px; top: 110px;
    list-style: none;
  }
  .service-item {
    display: flex;
    align-items: center;
    gap: 12px;
    height: 27.5px;
    font-size: 19px;
    color: var(--text-white);
  }
  .service-item::before {
    content: "";
    width: 9px; height: 9px;
    border-radius: 50%;
    background: var(--text-white);
  }
  .card--back .brand-name {
    left: 40px; top: 276px;
    font-size: 40px;
    color: var(--text-white);
  }
</style>
</head>
<body>
  <section class="card card--front">
    <div class="brand-name"><span class="brand-dot"></span>BRIGHT RIVER POWER</div>

    <ul class="contact-list">
      <li class="contact-item">
        <svg class="contact-icon" viewBox="0 0 24 24"><path d="M6.6 10.8c1.4 2.8 3.8 5.1 6.6 6.6l2.2-2.2c.3-.3.7-.4 1-.2 1.1.4 2.3.6 3.6.6.6 0 1 .4 1 1V20c0 .6-.4 1-1 1C10.6 21 3 13.4 3 4c0-.6.4-1 1-1h3.5c.6 0 1 .4 1 1 0 1.3.2 2.5.6 3.6.1.3 0 .7-.2 1L6.6 10.8z"/></svg>
        0438759164
      </li>
      <li class="contact-item">
        <svg class="contact-icon" viewBox="0 0 24 24"><path d="M2 5h20v14H2z M4 7v.4l8 5.2 8-5.2V7z" fill-rule="evenodd"/></svg>
        info@brightriverpower.net.au
      </li>
      <li class="contact-item">
        <svg class="contact-icon" viewBox="0 0 24 24"><circle cx="12" cy="12" r="10"/><path d="M7 6c2 1 3 3 2 5s1 3 2 5M15 4c-1 2 0 3 2 4s2 4 1 7" stroke="#fff" stroke-width="1.6" fill="none"/></svg>
        www.brightriverpower.net.au
      </li>
    </ul>

    <div class="contact-name">Dennis Halvorsen</div>
    <div class="name-tab"></div>
  </section>

  <section class="card card--back">
    <ul class="service-list">
      <li class="service-item">Solar</li>
      <li class="service-item">Battery storage</li>
      <li class="service-item">LED lighting</li>
      <li class="service-item">Energy saving solutions</li>
    </ul>
    <div class="brand-name">BRIGHT RIVER POWER</div>
  </section>
</body>
</html>
```